Awesome design needed for standup comedy portal

We need a website designed for a new portal (grinbox.net) dedicated to standup comedy.

- homepage
- featured "hero" content at top
- banner advertising
- browse comics
- browse venues
- search
- signup / login
- social media links

- comic page
- name
- pictures
- calendar of performances
- list of albums (with buy buttons)
- list of specials (Vexora, Plumtrack, etc. with buy buttons)
- reviews
- latest tweets
- latests pixaloop photos
- links to social media accounts
- links to filmdex, podcast

- venue page
- name
- pictures
- address, phone number
- calendar of events
- reviews
- latest tweets
- links to filmdex, podcast

Target Market(s)

Fans of standup comedy and comedians

Number of Pages Required

Font styles to use
Sans Serif

Requirements
Must have
• Will eventually be implemented in bootstrap, so please keep that in mind

```html
<!DOCTYPE html>
<html lang="en">
<head>
<meta charset="utf-8">
<title>Grinbox – Comic</title>
<link href="https://fonts.googleapis.com/css2?family=Open+Sans:wght@400;600;700;800&display=swap" rel="stylesheet">
<style>
:root{
  --red:#c4161c;
  --red-dark:#7a1416;
  --ink:#222;
  --text:#555;
  --muted:#999;
  --line:#e2e2e2;
  --dark-btn:#333;
  --footer:#2b2b2b;
  --footer-text:#bbb;
  --star:#b5c21a;
  --chirp:#1da1e2;
  --pix:#8a5a44;
}
*{box-sizing:border-box;margin:0;padding:0}
html,body{width:1200px;height:2691px;overflow:hidden;background:#fff}
body{position:relative;font-family:'Open Sans',sans-serif;color:var(--text)}
.abs{position:absolute}
a{color:inherit;text-decoration:none}

/* header */
.site-header{position:absolute;left:0;top:0;width:1200px;height:170px;background:linear-gradient(#f6f6f6,#ececec)}
.social{left:75px;top:62px;display:flex;align-items:center;gap:14px;font-size:13px;font-weight:700;color:var(--red)}
.social .dot{width:17px;height:17px;border-radius:3px;background:#666}
.search-field{top:56px;height:36px;border:1px solid #ccc;background:#fff;font-size:12px;color:#666;padding:9px 12px}
.search-btn{left:1089px;top:56px;width:36px;height:36px;background:var(--red)}
.brand{display:flex;flex-direction:column;align-items:center;gap:6px}
.brand .mark{border-radius:50%;background:var(--red)}
.brand .name{font-weight:800;color:var(--red);letter-spacing:1px}
.main-nav{top:132px;font-size:14px;font-weight:700;color:#333;letter-spacing:.5px}
.main-nav.active{color:var(--red)}
.nav-underline{left:408px;top:164px;width:78px;height:4px;background:var(--red)}
.btn-signup{left:933px;top:124px;width:90px;height:39px;background:var(--red-dark);color:#fff;font-size:13px;font-weight:700;display:flex;align-items:center;justify-content:center}
.btn-login{left:1037px;top:124px;width:88px;height:39px;border:2px solid var(--red-dark);color:#333;font-size:13px;font-weight:700;display:flex;align-items:center;justify-content:center}

/* common */
.section-title{font-size:24px;font-weight:800;color:var(--red);letter-spacing:.5px}
.section-title span{color:var(--ink)}
.divider{left:75px;width:1050px;height:2px;background:var(--line)}
.photo{position:absolute}
.arrows{display:flex;gap:6px}
.arrows i{display:block;width:20px;height:20px;border-radius:50%;border:2px solid #777;position:relative}
.arrows i::after{content:"";position:absolute;left:5px;top:5px;width:5px;height:5px;border-top:2px solid #777;border-left:2px solid #777;transform:rotate(-45deg)}
.arrows i.next::after{transform:rotate(135deg);left:3px}
.body-copy{font-size:14px;line-height:1.85;color:#555}
.card-title{font-size:13px;font-weight:800;color:var(--red)}
.card-text{font-size:14px;line-height:1.75;color:#555}
.btn-buy{width:77px;height:34px;color:#fff;font-size:12px;font-weight:700;display:flex;align-items:center;justify-content:center;border-radius:3px}
.btn-buy.red{background:var(--red)}
.btn-buy.dark{background:var(--dark-btn)}

/* calendar */
.calendar{left:703px;top:692px;width:422px;height:325px;border:1px solid var(--line)}
.cal-head{height:51px;background:#f1f1f1;display:flex;align-items:center;justify-content:space-between}
.cal-head b{font-size:15px;color:var(--red);font-weight:700}
.cal-arrow{width:28px;height:51px;background:var(--red);position:relative}
.cal-arrow::after{content:"";position:absolute;left:10px;top:21px;width:8px;height:8px;border-top:2px solid #fff;border-left:2px solid #fff;transform:rotate(-45deg)}
.cal-arrow.next::after{transform:rotate(135deg);left:7px}
.cal-grid{position:absolute;left:28px;top:70px;border-collapse:collapse}
.cal-grid th{width:52px;height:30px;font-size:11px;font-weight:700;color:#444}
.cal-grid td{width:52px;height:39px;border:1px solid var(--line);text-align:center;font-size:12px;color:#555}
.cal-grid td.off{color:#ccc}
.cal-grid td.today{background:var(--red);color:#fff;font-weight:700}

/* reviews & tweets */
.stars{font-size:15px;letter-spacing:1px;color:#aaa}
.stars em{font-style:normal;color:var(--star)}
.tweet-head{font-size:13px;font-weight:800;color:var(--chirp);display:flex;align-items:center;gap:6px}
.tweet-head i{width:11px;height:11px;border-radius:50%;background:var(--chirp);display:block}
.tweet-text{font-size:12.5px;line-height:1.9;color:#555}
.tweet-text a{color:var(--chirp)}
.feed-box{left:75px;top:2138px;width:508px;height:221px;border:2px solid #e4e4e4}
.feed-thumb{position:absolute;width:83px;height:84px;background:linear-gradient(135deg,#3a2a30,#8a6a60)}

/* footer */
.site-footer{position:absolute;left:0;top:2469px;width:1200px;height:222px;background:var(--footer)}
.foot-head{font-size:13px;font-weight:700;color:#fff;letter-spacing:.5px}
.foot-link{font-size:13px;color:var(--footer-text)}
.foot-icons{display:flex;gap:12px}
.foot-icons i{width:17px;height:17px;border-radius:3px;background:#777;display:block}
.news-input{left:884px;top:2544px;width:241px;height:39px;background:#777;color:#eee;font-size:13px;padding:10px 14px}
.news-btn{left:1037px;top:2594px;width:88px;height:34px;background:var(--red);color:#fff;font-size:13px;font-weight:700;display:flex;align-items:center;justify-content:center}
</style>
</head>
<body>

<!-- Header -->
<header class="site-header">
  <div class="abs social">SOCIAL: <i class="dot"></i><i class="dot"></i><i class="dot"></i><i class="dot"></i><i class="dot"></i></div>
  <div class="abs brand" style="left:530px;top:20px;width:140px">
    <div class="mark" style="width:76px;height:76px"></div>
    <div class="name" style="font-size:26px">GRINBOX</div>
  </div>
  <div class="abs search-field" style="left:712px;width:178px">Browse Comics</div>
  <div class="abs search-field" style="left:900px;width:177px">Browse Venues</div>
  <div class="abs search-btn">
    <svg width="36" height="36" viewBox="0 0 36 36"><circle cx="16" cy="16" r="6" fill="none" stroke="#fff" stroke-width="2.5"/><line x1="20.5" y1="20.5" x2="25" y2="25" stroke="#fff" stroke-width="2.5"/></svg>
  </div>
  <nav>
    <a class="abs main-nav" style="left:95px">HOME</a>
    <a class="abs main-nav" style="left:192px">ABOUT</a>
    <a class="abs main-nav" style="left:296px">SERVICES</a>
    <a class="abs main-nav active" style="left:415px">COMICS</a>
    <a class="abs main-nav" style="left:717px">VENUES</a>
    <a class="abs main-nav" style="left:828px">CONTACT</a>
  </nav>
  <div class="abs nav-underline"></div>
  <a class="abs btn-signup">SIGN UP</a>
  <a class="abs btn-login">LOG IN</a>
</header>

<!-- Comic intro -->
<section>
  <h1 class="abs section-title" style="left:75px;top:222px">COMIC</h1>
  <p class="abs body-copy" style="left:75px;top:270px;width:465px">Vestibulum vel metus sit amet turpis bibendum tincidunt vel sit amet quam. Pellentesque habitant morbi tristique senectus et netus et malesuada fames ac turpis egestas. Suspendisse lobortis turpis in odio blandit ac interdum lorem euismod ultrices posuere cubiliaSuspendisse lobortis turpis in odio blandit ac interdum lorem euismod ultrices posuere cubilia Pellentesque habitant morbi tristique senectus et netus et malesuada fames ac turpis egestas.</p>
  <a class="abs" style="left:75px;top:469px;font-size:11px;font-weight:800;color:var(--red-dark)">READ MORE »</a>
  <div class="abs brand" style="left:565px;top:275px;width:175px">
    <div class="mark" style="width:100px;height:100px"></div>
    <div class="name" style="font-size:32px">GRINBOX</div>
  </div>
  <div class="photo" role="img" aria-label="Comedian on stage with a ventriloquist puppet" style="left:762px;top:228px;width:363px;height:283px;background:radial-gradient(circle at 45% 40%,#3d6670,#14262c 70%)"></div>
</section>

<div class="abs divider" style="top:562px"></div>

<!-- Calendar -->
<section>
  <h2 class="abs section-title" style="left:0;width:1200px;text-align:center;top:610px">CALENDAR <span>OF PERFORMANCES</span></h2>
  <div class="photo" role="img" aria-label="Vintage microphone in front of a red stage curtain" style="left:75px;top:694px;width:591px;height:323px;background:radial-gradient(ellipse at 50% 45%,#d13a3a,#7a0c0f 55%,#2a0405)"></div>
  <div class="abs calendar">
    <div class="cal-head"><i class="cal-arrow"></i><b>MARCH</b><i class="cal-arrow next"></i></div>
    <table class="cal-grid">
      <tr><th>Mon</th><th>Tue</th><th>Wed</th><th>Thu</th><th>Fri</th><th>Sat</th><th>Sun</th></tr>
      <tr><td>1</td><td>2</td><td>3</td><td>4</td><td>5</td><td>6</td><td>7</td></tr>
      <tr><td>8</td><td>9</td><td>10</td><td>11</td><td>12</td><td>13</td><td>14</td></tr>
      <tr><td>15</td><td>16</td><td>17</td><td>18</td><td>19</td><td>20</td><td>21</td></tr>
      <tr><td>22</td><td>23</td><td>24</td><td>25</td><td>26</td><td>27</td><td>28</td></tr>
      <tr><td>29</td><td class="today">30</td><td>31</td><td class="off">1</td><td class="off">2</td><td class="off">3</td><td class="off">4</td></tr>
    </table>
  </div>
</section>

<div class="abs divider" style="top:1080px"></div>

<!-- Albums -->
<section>
  <h2 class="abs section-title" style="left:0;width:1200px;text-align:center;top:1125px">ALBUMS</h2>
  <div class="abs arrows" style="left:1077px;top:1147px"><i></i><i class="next"></i></div>

  <div class="photo" role="img" aria-label="Comedian holding an award on stage" style="left:75px;top:1200px;width:242px;height:156px;background:linear-gradient(135deg,#1c1c1c,#6a5030)"></div>
  <div class="abs card-title" style="left:75px;top:1372px">LOREM IPSUM DOLOR</div>
  <p class="abs card-text" style="left:75px;top:1395px;width:245px">Sit amet consect- etuer adipiscing elit, sed diam nonummy..</p>
  <a class="abs btn-buy red" style="left:75px;top:1457px">BUY</a>

  <div class="photo" role="img" aria-label="Ventriloquist performing with a puppet" style="left:342px;top:1200px;width:242px;height:156px;background:linear-gradient(135deg,#1d3238,#4a6a70)"></div>
  <div class="abs card-title" style="left:342px;top:1372px">LOREM IPSUM DOLOR</div>
  <p class="abs card-text" style="left:342px;top:1395px;width:245px">Sit amet consect- etuer adipiscing elit, sed diam nonummy..</p>
  <a class="abs btn-buy dark" style="left:342px;top:1457px">BUY</a>

  <div class="photo" role="img" aria-label="Comedian at a red carpet event" style="left:613px;top:1200px;width:242px;height:156px;background:linear-gradient(135deg,#b52a30,#7a1a20)"></div>
  <div class="abs card-title" style="left:613px;top:1372px">LOREM IPSUM DOLOR</div>
  <p class="abs card-text" style="left:613px;top:1395px;width:245px">Sit amet consect- etuer adipiscing elit, sed diam nonummy..</p>
  <a class="abs btn-buy dark" style="left:613px;top:1457px">BUY</a>

  <div class="photo" role="img" aria-label="Comedian on stage with a purple puppet" style="left:884px;top:1200px;width:242px;height:156px;background:linear-gradient(135deg,#141414,#4a4060)"></div>
  <div class="abs card-title" style="left:884px;top:1372px">LOREM IPSUM DOLOR</div>
  <p class="abs card-text" style="left:884px;top:1395px;width:245px">Sit amet consect- etuer adipiscing elit, sed diam nonummy..</p>
  <a class="abs btn-buy dark" style="left:884px;top:1457px">BUY</a>
</section>

<div class="abs divider" style="top:1521px"></div>

<!-- Specials -->
<section>
  <h2 class="abs section-title" style="left:75px;top:1568px">SPECIALS</h2>
  <div class="abs arrows" style="left:538px;top:1575px"><i></i><i class="next"></i></div>

  <div class="photo" role="img" aria-label="Comedian with a microphone on a blue stage" style="left:75px;top:1643px;width:242px;height:156px;background:linear-gradient(135deg,#2a5a90,#8ab0d8)"></div>
  <div class="abs card-title" style="left:75px;top:1826px"><span style="margin-right:12px">VEXORA</span>LOREM IPSUM DOLOR</div>
  <p class="abs card-text" style="left:75px;top:1850px;width:250px">Sit amet consect- etuer adipiscing elit, sed diam nonummy orem euis- mod ultrices posuere cubilia.....</p>
  <a class="abs btn-buy red" style="left:75px;top:1941px">BUY</a>

  <div class="photo" role="img" aria-label="Ventriloquist with a puppet on a dark blue stage" style="left:342px;top:1643px;width:242px;height:156px;background:linear-gradient(135deg,#0e1a38,#2a3a70)"></div>
  <div class="abs card-title" style="left:342px;top:1826px;color:var(--ink);display:flex;align-items:center;gap:8px"><i style="width:16px;height:16px;border-radius:50%;background:#2a6ad0;display:block"></i>PLUMTRACK · LOREM IPSUM DOLOR</div>
  <p class="abs card-text" style="left:342px;top:1850px;width:250px">Sit amet consect- etuer adipiscing elit, sed diam nonummy orem euis- mod ultrices posuere cubilia.....</p>
  <a class="abs btn-buy dark" style="left:342px;top:1941px">BUY</a>
</section>

<!-- Reviews -->
<section>
  <h2 class="abs section-title" style="left:628px;top:1568px">REVIEWS</h2>
  <div class="abs arrows" style="left:1077px;top:1575px"><i></i><i class="next"></i></div>
  <div class="abs" style="left:628px;top:1640px;width:497px">
    <div class="card-title">LOREM IPSUM DOLOR</div>
    <p class="card-text" style="font-size:13px;margin-top:6px">Vestibulum vel metus sit amet turpis bibendum tincidunt vel sit amet quam metus sit amet turpis bibendum tincidunt vel sit amet quam.</p>
    <div class="stars"><em>★★★</em>★★</div>
  </div>
  <div class="abs" style="left:628px;top:1762px;width:497px">
    <div class="card-title">LOREM IPSUM DOLOR</div>
    <p class="card-text" style="font-size:13px;margin-top:6px">Vestibulum vel metus sit amet turpis bibendum tincidunt vel sit amet quam metus sit amet turpis bibendum tincidunt vel sit amet quam.</p>
    <div class="stars"><em>★★★</em>★★</div>
  </div>
  <div class="abs" style="left:628px;top:1884px;width:497px">
    <div class="card-title">LOREM IPSUM DOLOR</div>
    <p class="card-text" style="font-size:13px;margin-top:6px">Vestibulum vel metus sit amet turpis bibendum tincidunt vel sit amet quam metus sit amet turpis bibendum tincidunt vel sit amet quam.</p>
    <div class="stars"><em>★★★</em>★★</div>
  </div>
</section>

<div class="abs divider" style="top:2031px"></div>

<!-- Photo feed -->
<section>
  <h2 class="abs section-title" style="left:75px;top:2083px;color:var(--pix);display:flex;align-items:center;gap:10px"><i style="width:22px;height:22px;background:var(--pix);display:block;border-radius:3px"></i>PIXALOOP FEED</h2>
  <div class="abs feed-box"></div>
  <div class="feed-thumb" role="img" aria-label="Feed photo of a puppet" style="left:93px;top:2153px"></div>
  <div class="feed-thumb" role="img" aria-label="Feed photo of a comedian" style="left:188px;top:2153px;background:linear-gradient(135deg,#1a1a1a,#5a4a3a)"></div>
  <div class="feed-thumb" role="img" aria-label="Feed photo of a comedian" style="left:285px;top:2153px;background:linear-gradient(135deg,#3a6aa0,#c0a080)"></div>
  <div class="feed-thumb" role="img" aria-label="Feed photo of a comedian" style="left:384px;top:2153px;background:linear-gradient(135deg,#111,#5a5a5a)"></div>
  <div class="feed-thumb" role="img" aria-label="Feed photo of a puppet" style="left:481px;top:2153px;background:linear-gradient(135deg,#4a2030,#c07080)"></div>
  <div class="feed-thumb" role="img" aria-label="Feed photo of a comedian" style="left:93px;top:2255px;background:linear-gradient(135deg,#111,#6a5a4a)"></div>
  <div class="feed-thumb" role="img" aria-label="Feed photo of a comedian on stage" style="left:188px;top:2255px;background:linear-gradient(135deg,#0e1a38,#3a4a80)"></div>
  <div class="feed-thumb" role="img" aria-label="Feed photo of a puppet" style="left:285px;top:2255px;background:linear-gradient(135deg,#3a1a20,#b07060)"></div>
  <div class="feed-thumb" role="img" aria-label="Feed photo of a puppet" style="left:384px;top:2255px;background:linear-gradient(135deg,#2a1010,#a05050)"></div>
  <div class="feed-thumb" role="img" aria-label="Feed photo of a comedian" style="left:481px;top:2255px;background:linear-gradient(135deg,#111,#4a4a4a)"></div>
</section>

<!-- Tweets -->
<section>
  <h2 class="abs section-title" style="left:617px;top:2083px;color:var(--chirp);display:flex;align-items:center;gap:10px"><i style="width:22px;height:22px;background:var(--chirp);display:block;border-radius:50%"></i>LATEST TWEETS</h2>
  <div class="abs" style="left:617px;top:2134px;width:508px">
    <div class="tweet-head"><i></i>LOREM IPSUM @TWIPSUM &nbsp;10 MAR 2017</div>
    <p class="tweet-text">Duis ultrices vestibulum lacus non luctus. Praesent aliquet, <a>justo ut</a> accumsan bibendum, <a>sem erat sagittis</a> nunc...</p>
  </div>
  <div class="abs" style="left:617px;top:2231px;width:508px">
    <div class="tweet-head"><i></i>LOREM IPSUM @TWIPSUM &nbsp;10 MAR 2017</div>
    <p class="tweet-text">Duis ultrices vestibulum lacus non luctus. Praesent bibendum, <a>sem erat</a> nunc...</p>
  </div>
  <div class="abs" style="left:617px;top:2301px;width:508px">
    <div class="tweet-head"><i></i>LOREM IPSUM @TWIPSUM &nbsp;10 MAR 2017</div>
    <p class="tweet-text">Duis ultrices vestibulum lacus non luctus. Praesent aliquet, <a>justo ut</a> accumsan bibendum, <a>sem erat sagittis</a> nunc...</p>
  </div>
</section>

<!-- Footer -->
<footer class="site-footer">
  <p class="abs foot-link" style="left:75px;top:78px;font-size:11.5px;line-height:1.7">Copyright © 2017, Grinbox<br>All Right Reserved</p>
  <div class="abs foot-icons" style="left:75px;top:128px"><i></i><i></i><i></i><i></i><span style="font-size:12px;font-weight:700;color:#999;line-height:17px">filmdex</span>
    <svg width="18" height="17" viewBox="0 0 18 17"><path d="M3 11V9a6 6 0 0 1 12 0v2" fill="none" stroke="#999" stroke-width="2"/><rect x="2" y="10" width="4" height="6" rx="1" fill="#999"/><rect x="12" y="10" width="4" height="6" rx="1" fill="#999"/></svg>
  </div>

  <div class="abs foot-head" style="left:357px;top:42px">QUICK LINKS</div>
  <a class="abs foot-link" style="left:357px;top:71px">Home</a>
  <a class="abs foot-link" style="left:357px;top:101px">About</a>
  <a class="abs foot-link" style="left:357px;top:130px">Services</a>
  <a class="abs foot-link" style="left:456px;top:71px">Comics</a>
  <a class="abs foot-link" style="left:456px;top:101px">Venues</a>
  <a class="abs foot-link" style="left:456px;top:130px">Contact</a>

  <div class="abs foot-head" style="left:615px;top:42px">CONTACT INFO</div>
  <p class="abs foot-link" style="left:615px;top:69px;line-height:1.7">4120 Larkspur Lane<br>Glasgow, G12 7QT</p>
  <div class="abs foot-link" style="left:615px;top:121px;display:flex;gap:20px;align-items:center">
    <svg width="12" height="12" viewBox="0 0 12 12"><path d="M2 1h3l1 3-2 1a7 7 0 0 0 3 3l1-2 3 1v3c-6 0-9-3-9-9z" fill="#bbb"/></svg>1-800-555-0142</div>
  <div class="abs foot-link" style="left:615px;top:150px;display:flex;gap:20px;align-items:center">
    <svg width="12" height="10" viewBox="0 0 12 10"><rect width="12" height="10" fill="#bbb"/><path d="M0 0l6 5 6-5" fill="none" stroke="#2b2b2b" stroke-width="1.2"/></svg>info@grinbox.net</div>

  <div class="abs foot-head" style="left:884px;top:42px">NEWSLETTER SIGN UP</div>
</footer>
<div class="abs news-input">Enter Email Address</div>
<a class="abs news-btn">SIGN UP</a>

<div class="abs brand" style="left:75px;top:2404px;width:140px;align-items:flex-start">
  <div class="mark" style="width:70px;height:70px;margin-left:30px"></div>
  <div class="name" style="font-size:24px">GRINBOX</div>
</div>

</body>
</html>
```